International Clinical Software Company needs a new business card design

We are looking for a new business card design for our company that has recently expanded into the UK market, making us a multinational company.
After having rebranded our website and produced a new style guide, we are looking for a business card that is creative and attention grabbing, while being consistent with the style and colour scheme used on the new website, www.plumvora.example
We produce care management technology for the aged care market, but the main aspect we aim to communicate is the human element of our software, and the way it assists in providing better care for aged people, and stronger relationships between aged people and the staff that care for them.
Our current business card is a dark green with gold text, which makes the text quite difficult to read, not very aesthetically appealing and the colour scheme looks quite dated.
We would like something fresh and modern, that can still be colourful but doesn't use large blocks of dark colour, and uses the colours within our logo.
Something tying in with the leaves that are used in our logo could work quite nicely, along with the Autumn/Fall colours of soft greens, yellows and reds (also in our existing logo). However also happy to look at fresh, completely out of the box ideas we may not have yet considered.
Target Market(s)
The people that receive this business card work in the aged card or health industry and are either corporate/management level staff or clinical (Registered Nurses, care workers etc.)
Industry/Entity Type
Health Product
Contact Information for Business Card
Company Name - BrindlewayCare
Company locations: United Kingdom, Australia, New Zealand
Staff Details:
Staff name: Derek Mallow
Staff job title: Executive Chairman
Staff email: d.mallow@plumvora.example
Office phone number: 01742 918576
Font styles to use
Other font styles liked:
- Calibri
Requirements
Must have
- Must include the BrindlewayCare brand name in it's current font
- Must include logo (3 leaves in gold circle)
- Must include Business Card Details
Nice to have
- Elements of gold
- White space
- Something autumn themed but not too cliched
Should not have
- No blue - used by a major competitor and we would like to differentiate from them
- Large blocks of dark green colour (the green that appears in our leaves on the logo on our current business card is the background colour and it is far too dark)

```html
<!DOCTYPE html>
<html lang="en">
<head>
<meta charset="utf-8">
<title>BrindlewayCare – Business Card</title>
<link rel="stylesheet" href="https://fonts.googleapis.com/css2?family=Carlito:wght@400;700&display=swap">
<style>
  :root {
    --backdrop: #e9e9ea;
    --card: #f3f3f5;
    --gold: #a8946a;
    --berry: #940436;
    --on-berry: #f4e9ee;
  }
  html, body {
    margin: 0;
    width: 1105px;
    height: 1200px;
    overflow: hidden;
    background: var(--backdrop);
    font-family: "Carlito", Calibri, sans-serif;
  }
  .business-card {
    position: absolute;
    left: 52px;
    top: 315px;
    width: 1000px;
    height: 570px;
    background: var(--card);
    overflow: hidden;
    box-shadow: 0 2px 6px rgba(0,0,0,0.12);
  }
  .brand-mark {
    position: absolute;
    left: 192px;
    top: 70px;
    width: 134px;
    height: 134px;
    border-radius: 50%;
    background: var(--gold);
  }
  .brand-name {
    position: absolute;
    left: 76px;
    top: 222px;
    margin: 0;
    font-size: 62px;
    font-weight: 400;
    color: var(--gold);
    letter-spacing: 0.5px;
  }
  .holder {
    position: absolute;
    left: 76px;
    top: 418px;
  }
  .holder-name {
    margin: 0;
    font-size: 37px;
    font-weight: 700;
    color: var(--gold);
    line-height: 1.1;
  }
  .holder-role {
    margin: 4px 0 0;
    font-size: 30px;
    color: var(--berry);
  }
  .contact-disc {
    position: absolute;
    left: 0;
    top: 0;
  }
  .contact-panel {
    position: absolute;
    right: 67px;
    top: 318px;
    text-align: right;
    color: var(--on-berry);
    font-size: 28px;
    line-height: 36px;
  }
  .locations { margin: 0 0 12px; }
  .contact-list { list-style: none; margin: 0; padding: 0; }
  .contact-list li {
    display: flex;
    justify-content: flex-end;
    align-items: center;
    gap: 14px;
    height: 38px;
  }
  .contact-icon { width: 24px; height: 24px; flex: none; }
</style>
</head>
<body>
  <article class="business-card">
    <svg class="contact-disc" width="1000" height="570" aria-hidden="true">
      <circle cx="822" cy="476" r="294" fill="none" stroke="var(--gold)" stroke-width="5"/>
      <circle cx="822" cy="476" r="284" fill="var(--berry)"/>
    </svg>

    <div class="brand-mark" aria-hidden="true"></div>
    <h1 class="brand-name">BrindlewayCare</h1>

    <div class="holder">
      <p class="holder-name">Derek Mallow</p>
      <p class="holder-role">Executive Chairman</p>
    </div>

    <div class="contact-panel">
      <p class="locations">United Kingdom<br>Australia, New Zealand</p>
      <ul class="contact-list">
        <li>01742 918576
          <svg class="contact-icon" viewBox="0 0 24 24" aria-label="Phone"><path fill="var(--on-berry)" d="M6.6 10.8c1.4 2.8 3.8 5.1 6.6 6.6l2.2-2.2c.3-.3.7-.4 1-.2 1.1.4 2.3.6 3.6.6.6 0 1 .4 1 1V20c0 .6-.4 1-1 1C10.6 21 3 13.4 3 4c0-.6.4-1 1-1h3.5c.6 0 1 .4 1 1 0 1.3.2 2.5.6 3.6.1.3 0 .7-.2 1z"/></svg>
        </li>
        <li>d.mallow@plumvora.example
          <svg class="contact-icon" viewBox="0 0 24 24" aria-label="Email"><rect x="2" y="5" width="20" height="14" rx="1" fill="var(--on-berry)"/><path d="M2.5 5.5 12 13l9.5-7.5" fill="none" stroke="var(--berry)" stroke-width="1.6"/></svg>
        </li>
        <li>www.plumvora.example
          <svg class="contact-icon" viewBox="0 0 24 24" aria-label="Website"><circle cx="12" cy="12" r="10" fill="var(--on-berry)"/><path d="M2 12h20M12 2c3 3 3 17 0 20M12 2c-3 3-3 17 0 20" fill="none" stroke="var(--berry)" stroke-width="1.4"/></svg>
        </li>
      </ul>
    </div>
  </article>
</body>
</html>
```